stationary deign for trucking company

im a trucking company looking for a professional set of stationary designs i deliver goods from point a to b
Updates

When submitting stationary designs I need envelope design, letterhead, cards, I’d badge etc

Industry/Entity Type

Trucking Company

Requirements
Must have
• must have letter head, business card, envelope, fax sheet, id badge, folder, thank you card, notebook, invoice sheet.
Nice to have
• nice to have them all custom made (letterhead,envelope, business card, I’d badge etc
Should not have
• must not have prepaid sign want i unique design for items

```html
<!DOCTYPE html>
<html lang="en">
<head>
<meta charset="utf-8">
<title>Harrow Freight – Business Card</title>
<link href="https://fonts.googleapis.com/css2?family=Roboto:wght@400;500&display=swap" rel="stylesheet">
<style>
  :root {
    --page-bg: #e6e6e6;
    --card-white: #ffffff;
    --brand-blue: #0755a3;
    --ink-black: #111111;
    --ink-grey: #555555;
  }
  html, body {
    margin: 0;
    padding: 0;
    width: 1125px;
    height: 1200px;
    overflow: hidden;
    background: var(--page-bg);
    font-family: "Roboto", Arial, sans-serif;
  }
  .card {
    position: absolute;
    left: 156px;
    width: 826px;
    height: 471px;
    box-shadow: 0 14px 30px rgba(0,0,0,0.18);
  }
  .card--front { top: 106px; background: var(--card-white); }
  .card--back  { top: 639px; background: var(--brand-blue); }

  .brand {
    position: absolute;
    left: 52px;
    top: 64px;
    display: flex;
    align-items: center;
    gap: 18px;
  }
  .brand__square {
    width: 40px;
    height: 40px;
    background: var(--brand-blue);
  }
  .brand__name {
    font-size: 30px;
    font-weight: 500;
    letter-spacing: 4px;
    color: var(--ink-black);
  }

  .contact-row {
    position: absolute;
    left: 0;
    width: 560px;
  }
  .contact-row__icon {
    position: absolute;
    left: 74px;
    width: 18px;
    height: 18px;
    fill: var(--brand-blue);
  }
  .contact-row__text {
    position: absolute;
    left: 137px;
    margin: 0;
    font-size: 19px;
    line-height: 25px;
    color: var(--ink-grey);
    white-space: nowrap;
  }
  .person-name {
    font-size: 30px;
    font-weight: 500;
    color: var(--brand-blue);
    line-height: 32px;
  }
  .person-title {
    font-size: 20px;
    font-weight: 500;
    color: var(--ink-black);
    line-height: 26px;
  }

  .back-brand {
    position: absolute;
    left: 0;
    right: 0;
    top: 205px;
    text-align: center;
    font-size: 48px;
    font-weight: 500;
    letter-spacing: 5px;
    color: var(--card-white);
  }
  .back-web {
    position: absolute;
    left: 0;
    right: 0;
    top: 408px;
    text-align: center;
    font-size: 19px;
    letter-spacing: 9px;
    color: var(--card-white);
  }
</style>
</head>
<body>

<section class="card card--front">
  <div class="brand">
    <div class="brand__square"></div>
    <div class="brand__name">HARROW FREIGHT</div>
  </div>

  <div class="contact-row" style="top:152px">
    <svg class="contact-row__icon" style="top:8px" viewBox="0 0 18 18"><circle cx="9" cy="5" r="4"/><path d="M1 17c0-5 3.5-7 8-7s8 2 8 7z"/></svg>
    <div class="contact-row__text">
      <div class="person-name">DANIEL REYES</div>
      <div class="person-title">CEO/FOUNDER</div>
    </div>
  </div>

  <div class="contact-row" style="top:226px">
    <svg class="contact-row__icon" style="top:6px;height:22px" viewBox="0 0 18 22"><path d="M9 0a8 8 0 0 0-8 8c0 6 8 14 8 14s8-8 8-14a8 8 0 0 0-8-8zm0 11a3 3 0 1 1 0-6 3 3 0 0 1 0 6z"/></svg>
    <p class="contact-row__text">1420 Larchmont Road<br>Fairbanks, Alaska 99701</p>
  </div>

  <div class="contact-row" style="top:289px">
    <svg class="contact-row__icon" style="top:4px" viewBox="0 0 18 18"><path d="M4 1l3 4-2 2c1 2.5 3.5 5 6 6l2-2 4 3-2 3C8 17 1 10 1 3z"/></svg>
    <p class="contact-row__text">555 214 3870</p>
  </div>
  <div class="contact-row" style="top:315px">
    <svg class="contact-row__icon" style="top:3px;height:20px" viewBox="0 0 18 20"><path d="M4 0h10a1 1 0 0 1 1 1v18a1 1 0 0 1-1 1H4a1 1 0 0 1-1-1V1a1 1 0 0 1 1-1zm1 3v12h8V3z"/></svg>
    <p class="contact-row__text">555 392 6148</p>
  </div>
  <div class="contact-row" style="top:341px">
    <svg class="contact-row__icon" style="top:4px;height:20px" viewBox="0 0 18 20"><path d="M4 0h9v6H4z"/><path d="M0 8h18v8h-3v4H3v-4H0zm5 6v4h8v-4z"/></svg>
    <p class="contact-row__text">555 718 2053</p>
  </div>
  <div class="contact-row" style="top:367px">
    <svg class="contact-row__icon" style="top:6px;height:14px" viewBox="0 0 18 14"><path d="M0 0h18v14H0zm2 2v1l7 5 7-5V2z"/></svg>
    <p class="contact-row__text">daniel@harrowfreight.com</p>
  </div>
  <div class="contact-row" style="top:393px">
    <svg class="contact-row__icon" style="top:4px" viewBox="0 0 18 18"><circle cx="9" cy="9" r="8.5"/><path d="M5 4c2 1 3 3 2 5s-3 2-3 4M12 3c-1 2 1 3 2 4M11 16c0-2 1-3 3-4" stroke="#fff" stroke-width="1.4" fill="none"/></svg>
    <p class="contact-row__text">www.harrowfreight.com</p>
  </div>
</section>

<section class="card card--back">
  <div class="back-brand">HARROW FREIGHT</div>
  <div class="back-web">www.harrowfreight.com</div>
</section>

</body>
</html>
```